Awesome photographers card for an awesome new business

Double sided business card Black background and silver logo in middle on one side. Details on otherside. please keep it simple

Industry/Entity Type

Photographer

Contact Information for Business Card

Gerald Fenwick
0452817360
GeraldFenwickPhotography47@mailbox.test
www.GeraldFenwickPhotography.test.au
Instagram _Gerald_fenwick

Requirements
Must have
• My logo in Silver
• please use instagram logo instead of "Instagram"

```html
<!DOCTYPE html>
<html lang="en">
<head>
<meta charset="utf-8">
<title>Gerald Fenwick Photography – Round Business Card</title>
<link rel="stylesheet" href="https://fonts.googleapis.com/css2?family=Source+Sans+3:wght@400;600&display=swap">
<style>
  :root {
    --backdrop: #393939;
    --card: #151515;
    --silver: #c4c4c4;
    --text-grey: #a6a6a6;
    --name-grey: #a9a9a9;
    --rule: #6a6a6a;
    --icon-grey: #9a9a9a;
  }
  html, body {
    margin: 0;
    padding: 0;
    width: 1200px;
    height: 900px;
    overflow: hidden;
    background: var(--backdrop);
  }
  .canvas {
    position: relative;
    width: 1200px;
    height: 900px;
    font-family: "Source Sans 3", sans-serif;
  }
  .card {
    position: absolute;
    top: 215px;
    width: 414px;
    height: 414px;
    border-radius: 50%;
    background: var(--card);
    box-shadow: 0 2px 6px rgba(0,0,0,0.35);
  }
  .card--front { left: 164px; }
  .card--back { left: 623px; }

  .brand {
    position: absolute;
    left: 0;
    right: 0;
    top: 192px;
    text-align: center;
    color: var(--silver);
    font-weight: 600;
    font-size: 25px;
    letter-spacing: 3px;
  }

  .holder-name {
    position: absolute;
    left: 0;
    right: 0;
    top: 92px;
    margin: 0;
    text-align: center;
    color: var(--name-grey);
    font-weight: 600;
    font-size: 25px;
    letter-spacing: 0.3px;
  }
  .rule {
    position: absolute;
    left: 126px;
    width: 162px;
    height: 1px;
    background: var(--rule);
  }
  .rule--top { top: 147px; }
  .rule--bottom { top: 296px; }

  .contact-icons {
    position: absolute;
    left: 0;
    right: 0;
    top: 175px;
    display: flex;
    justify-content: center;
    gap: 3px;
  }
  .contact-list {
    position: absolute;
    left: 0;
    right: 0;
    top: 199px;
    margin: 0;
    padding: 0;
    list-style: none;
    text-align: center;
    color: var(--text-grey);
    font-size: 19px;
    line-height: 24.5px;
  }
  .social {
    position: absolute;
    left: 0;
    right: 0;
    top: 317px;
    display: flex;
    justify-content: center;
    align-items: center;
    gap: 6px;
    color: var(--text-grey);
    font-size: 19px;
  }
  .social__mark {
    width: 20px;
    height: 20px;
    border-radius: 3px;
    background: var(--icon-grey);
  }
</style>
</head>
<body>
<main class="canvas">
  <section class="card card--front" aria-label="Card front">
    <div class="brand">GERALD FENWICK</div>
  </section>

  <section class="card card--back" aria-label="Card back">
    <h1 class="holder-name">GERALD FENWICK</h1>
    <div class="rule rule--top"></div>

    <div class="contact-icons" aria-hidden="true">
      <svg width="13" height="13" viewBox="0 0 24 24"><path fill="var(--icon-grey)" d="M6.6 10.8a15.1 15.1 0 0 0 6.6 6.6l2.2-2.2c.3-.3.7-.4 1-.2 1.1.4 2.3.6 3.6.6.6 0 1 .4 1 1V20c0 .6-.4 1-1 1A17 17 0 0 1 3 4c0-.6.4-1 1-1h3.5c.6 0 1 .4 1 1 0 1.3.2 2.5.6 3.6.1.3 0 .7-.2 1z"/></svg>
      <svg width="13" height="13" viewBox="0 0 24 24"><rect x="2" y="5" width="20" height="14" fill="var(--icon-grey)"/><path d="M2 5l10 8 10-8" fill="none" stroke="var(--card)" stroke-width="1.8"/></svg>
      <svg width="13" height="13" viewBox="0 0 24 24"><circle cx="12" cy="12" r="10" fill="var(--icon-grey)"/><path d="M2 12h20M12 2c3 3 3 17 0 20M12 2c-3 3-3 17 0 20" fill="none" stroke="var(--card)" stroke-width="1.5"/></svg>
    </div>

    <ul class="contact-list">
      <li class="contact-list__phone">0452817360</li>
      <li class="contact-list__email">GeraldFenwickPhotography47@mailbox.test</li>
      <li class="contact-list__web">www.GeraldFenwickPhotography.test.au</li>
    </ul>

    <div class="rule rule--bottom"></div>

    <div class="social">
      <span class="social__mark" aria-hidden="true"></span>
      <span class="social__handle">Gerald_fenwick</span>
    </div>
  </section>
</main>
</body>
</html>
```